Business Card Design Project

I have established a company called "Corvella" which is a business specialising in psychotherapy/counselling , predominantly for anxiety & depression.

My name is Nel....hence, the Corvella link. However, Corvella was also chosen for its reference to green shoots of growth/recovery.

Corvella is to be "upmarket" and highly professional. I'm keen for the style and colours to reflect this.....taupe/grey with navy/black script, for example.....NO primary colours.

My name needs to be on the card and my mobile number. Not sure, but suspect it should also have my qualifications ( BA (Psych) & BSc (Hons) Psychology). Mobile number 0412 903 618.

```html
<!DOCTYPE html>
<html lang="en">
<head>
<meta charset="utf-8">
<title>Corvella – Business Card Fronts</title>
<link rel="stylesheet" href="https://fonts.googleapis.com/css2?family=Federo&family=PT+Sans:wght@400;700&family=Oswald:wght@600&display=swap">
<style>
  :root {
    --page: #ffffff;
    --brand-green: #8aa85a;
    --name-navy: #2b3170;
    --ink: #1a1a1a;
    --tagline: #ffffff;
    --taupe-light: #ddd4c9;
    --taupe-deep: #a5978a;
    --navy: #232a66;
    --lavender: #d6d4e4;
    --grey-light: #f2f2f2;
    --grey-dark: #2e2e2e;
    --umber-light: #8c7d70;
    --umber-deep: #4a3f37;
    --label: #111111;
  }
  html, body {
    margin: 0;
    padding: 0;
    width: 1026px;
    height: 1200px;
    overflow: hidden;
    background: var(--page);
  }
  .sheet {
    position: relative;
    width: 1026px;
    height: 1200px;
  }
  .card {
    position: absolute;
    display: block;
    filter: drop-shadow(7px 7px 5px rgba(0,0,0,0.55));
  }
  .card--taupe { left: 232px; top: 162px; width: 367px; height: 207px; }
  .card--white { left: 284px; top: 510px; width: 360px; height: 204px; }

  .brand-name { font-family: "Federo", sans-serif; font-size: 20px; fill: var(--brand-green); }
  .person-name { font-family: "Federo", sans-serif; font-size: 26px; fill: var(--name-navy); }
  .credential { font-family: "PT Sans", sans-serif; font-size: 7.4px; fill: var(--ink); }
  .tagline { font-family: "PT Sans", sans-serif; font-size: 10px; fill: var(--tagline); }

  .side-label {
    position: absolute;
    margin: 0;
    font-family: "Oswald", sans-serif;
    font-weight: 600;
    font-size: 20px;
    color: var(--label);
  }
  .side-label--taupe { left: 260px; top: 374px; }
  .side-label--white { left: 310px; top: 722px; }
</style>
</head>
<body>
<main class="sheet">

  <svg class="card card--taupe" viewBox="0 0 260 147" preserveAspectRatio="none" aria-label="Card front, taupe version">
    <defs>
      <linearGradient id="taupeField" x1="0" y1="0" x2="1" y2="0">
        <stop offset="0" stop-color="var(--taupe-light)"/>
        <stop offset="0.6" stop-color="var(--taupe-deep)"/>
        <stop offset="1" stop-color="var(--taupe-deep)"/>
      </linearGradient>
      <linearGradient id="greySwoopTaupe" x1="0" y1="0" x2="1" y2="0">
        <stop offset="0" stop-color="var(--grey-light)"/>
        <stop offset="1" stop-color="var(--grey-dark)"/>
      </linearGradient>
      <linearGradient id="umberSwoopTaupe" x1="0" y1="1" x2="1" y2="0">
        <stop offset="0" stop-color="var(--umber-light)"/>
        <stop offset="1" stop-color="var(--umber-deep)"/>
      </linearGradient>
      <linearGradient id="navyBandTaupe" x1="0" y1="0" x2="1" y2="0">
        <stop offset="0" stop-color="var(--lavender)"/>
        <stop offset="0.55" stop-color="var(--navy)"/>
        <stop offset="1" stop-color="var(--navy)"/>
      </linearGradient>
    </defs>
    <rect class="field" width="260" height="147" fill="url(#taupeField)"/>
    <path class="base-sweep" d="M0,96 C80,104 160,108 226,104 C200,128 160,144 130,147 L0,147 Z" fill="var(--page)"/>
    <path class="grey-swoop" d="M208,0 C240,28 256,70 248,147 L260,147 L260,0 Z" fill="url(#greySwoopTaupe)"/>
    <path class="accent-swoop" d="M188,147 C222,132 248,104 260,62 L260,147 Z" fill="url(#umberSwoopTaupe)"/>
    <path class="navy-band" d="M0,96 C80,104 160,108 226,104 C180,128 110,145 40,147 L0,147 Z" fill="url(#navyBandTaupe)"/>
    <text class="brand-name" x="15" y="52">Corvella</text>
    <text class="person-name" x="208" y="52" text-anchor="end">NEL</text>
    <text class="credential" x="208" y="66" text-anchor="end">BA (Psych)</text>
    <text class="credential" x="208" y="78" text-anchor="end">BSc (Hons) Psychology</text>
    <text class="credential" x="208" y="91" text-anchor="end">Mobile: 0412 903 618</text>
    <text class="tagline" x="14" y="121">specialising in psychotherapy</text>
  </svg>
  <p class="side-label side-label--taupe">Front</p>

  <svg class="card card--white" viewBox="0 0 260 147" preserveAspectRatio="none" aria-label="Card front, white version">
    <defs>
      <linearGradient id="greySwoopWhite" x1="0" y1="0" x2="1" y2="0">
        <stop offset="0" stop-color="var(--grey-light)"/>
        <stop offset="1" stop-color="var(--grey-dark)"/>
      </linearGradient>
      <linearGradient id="umberSwoopWhite" x1="0" y1="1" x2="1" y2="0">
        <stop offset="0" stop-color="var(--umber-light)"/>
        <stop offset="1" stop-color="var(--umber-deep)"/>
      </linearGradient>
      <linearGradient id="navyBandWhite" x1="0" y1="0" x2="1" y2="0">
        <stop offset="0" stop-color="var(--lavender)"/>
        <stop offset="0.6" stop-color="var(--navy)"/>
        <stop offset="1" stop-color="var(--navy)"/>
      </linearGradient>
    </defs>
    <rect class="field" width="260" height="147" fill="var(--page)"/>
    <path class="grey-swoop" d="M208,0 C240,28 256,70 248,147 L260,147 L260,0 Z" fill="url(#greySwoopWhite)"/>
    <path class="accent-swoop" d="M188,147 C222,132 248,104 260,62 L260,147 Z" fill="url(#umberSwoopWhite)"/>
    <path class="navy-band" d="M0,94 C80,102 160,106 226,102 C180,126 110,142 0,142 Z" fill="url(#navyBandWhite)"/>
    <text class="brand-name" x="13" y="50">Corvella</text>
    <text class="person-name" x="210" y="50" text-anchor="end">NEL</text>
    <text class="credential" x="210" y="65" text-anchor="end">BA (Psych)</text>
    <text class="credential" x="210" y="77" text-anchor="end">BSc (Hons) Psychology</text>
    <text class="credential" x="210" y="90" text-anchor="end">Mobile: 0412 903 618</text>
    <text class="tagline" x="13" y="120">specialising in psychotherapy</text>
  </svg>
  <p class="side-label side-label--white">Front</p>

</main>
</body>
</html>
```